iOS7 test prep app

I need 3 basic screens and 2 product images for an iOS7 app I am prototyping. I provided lots of detail in the attached brief. This is an education product, so warm colors (especially reds) work best.

If you've done flat design for mobile products, please take a look ... Thanks!

Greetings, all. Thank you for your submissions. I am meeting with my product development team this week to review your submissions, and will select a designer before the end of the week. I appreciate your patience with my process, and thank you again for your interest in my project. I'll be back to you soon ... -Gerald

```html
<!DOCTYPE html>
<html lang="en">
<head>
<meta charset="utf-8">
<title>Quill Apps – Question 7 of 100</title>
<link rel="stylesheet" href="https://fonts.googleapis.com/css2?family=Roboto+Condensed:wght@400;700&family=Open+Sans:wght@400;600&display=swap">
<style>
  :root {
    --ink: #0b0b0b;
    --status-bg: #000000;
    --brand-red: #ec1c24;
    --bar-dark: #1a1a1a;
    --accent-green: #1fb53a;
    --green-panel: rgba(32, 140, 52, 0.92);
    --option-dark: rgba(28, 28, 28, 0.88);
    --option-text: #b9b9b9;
    --icon-green: #1e7a30;
    --icon-dark: #0f3316;
    --button-red: #cf2b30;
    --button-green: #24903a;
    --white: #ffffff;
    --photo-top: #6e6a66;
    --photo-mid: #8a8179;
    --photo-low: #5d5b59;
  }
  * { box-sizing: border-box; margin: 0; padding: 0; }
  html, body { width: 1200px; height: 2174px; overflow: hidden; background: var(--ink); }
  .screen { position: relative; width: 1200px; height: 2174px; overflow: hidden; font-family: "Open Sans", sans-serif; color: var(--white); }

  .status-bar { position: absolute; left: 0; top: 0; width: 1200px; height: 90px; background: var(--status-bg); font-family: "Roboto Condensed", sans-serif; font-weight: 700; font-size: 44px; }
  .status-bar .carrier { position: absolute; left: 20px; top: 20px; display: flex; align-items: center; gap: 10px; }
  .status-bar .time { position: absolute; left: 0; right: 0; top: 18px; text-align: center; }
  .status-bar .status-icons { position: absolute; right: 16px; top: 22px; }

  .app-header { position: absolute; left: 0; top: 90px; width: 1200px; height: 186px; background: var(--brand-red); }
  .app-header .title { position: absolute; left: 0; right: 0; top: 42px; text-align: center; font-family: "Roboto Condensed", sans-serif; font-size: 92px; line-height: 100px; font-weight: 400; }
  .app-header .back { position: absolute; left: 50px; top: 58px; }
  .app-header .menu { position: absolute; left: 1070px; top: 66px; }

  .question-bar { position: absolute; left: 0; top: 276px; width: 1200px; height: 189px; background: var(--bar-dark); }
  .question-bar .counter { position: absolute; left: 51px; top: 62px; font-family: "Roboto Condensed", sans-serif; font-size: 54px; line-height: 64px; color: var(--accent-green); }
  .question-bar .next-arrow { position: absolute; left: 1120px; top: 66px; }

  .backdrop { position: absolute; left: 0; top: 465px; width: 1200px; height: 1709px;
    background: radial-gradient(ellipse at 30% 20%, #9a8c80 0%, transparent 55%),
                radial-gradient(ellipse at 75% 40%, #8f8a84 0%, transparent 50%),
                linear-gradient(180deg, var(--photo-top), var(--photo-mid) 45%, var(--photo-low)); }

  .question-mark { position: absolute; left: 34px; top: 506px; width: 150px; height: 150px; border-radius: 50%; background: var(--icon-green); color: var(--ink); font-family: "Roboto Condensed", sans-serif; font-weight: 700; font-size: 110px; line-height: 150px; text-align: center; }

  .question-bubble { position: absolute; left: 218px; top: 508px; width: 946px; height: 259px; background: var(--green-panel); border-radius: 6px; padding: 26px 40px; font-size: 31px; line-height: 53px; font-weight: 600; }
  .question-bubble::before { content: ""; position: absolute; left: -22px; top: 62px; border-style: solid; border-width: 22px 22px 22px 0; border-color: transparent var(--green-panel) transparent transparent; }

  .option { position: absolute; left: 218px; width: 946px; height: 111px; background: var(--option-dark); border-radius: 5px; font-family: "Roboto Condensed", sans-serif; font-size: 37px; line-height: 111px; padding-left: 38px; color: var(--option-text); }
  .option .mark { position: absolute; left: 865px; top: 19px; }
  .option-a { top: 796px; }
  .option-b { top: 937px; }
  .option-c { top: 1077px; background: var(--green-panel); color: var(--white); }
  .option-d { top: 1217px; }

  .explanation { position: absolute; left: 218px; top: 1367px; width: 946px; height: 262px; background: var(--green-panel); border-radius: 5px; padding: 24px 40px; font-size: 31px; line-height: 53px; }
  .explanation .verdict { color: var(--ink); font-size: 34px; }

  .action { position: absolute; top: 1696px; width: 435px; height: 102px; border-radius: 4px; font-family: "Roboto Condensed", sans-serif; font-size: 46px; line-height: 102px; text-align: center; color: var(--white); }
  .action-save { left: 218px; background: var(--button-red); }
  .action-next { left: 729px; background: var(--button-green); }
</style>
</head>
<body>
<main class="screen">
  <div class="status-bar">
    <div class="carrier">
      <svg width="66" height="34" viewBox="0 0 66 34" aria-hidden="true">
        <rect x="0" y="22" width="9" height="12" fill="#fff"/><rect x="13" y="17" width="9" height="17" fill="#fff"/>
        <rect x="26" y="12" width="9" height="22" fill="#fff"/><rect x="39" y="6" width="9" height="28" fill="#fff"/>
        <rect x="52" y="0" width="9" height="34" fill="#fff"/>
      </svg>
      <span>Vela</span>
    </div>
    <div class="time">4:20 PM</div>
    <svg class="status-icons" width="300" height="50" viewBox="0 0 300 50" aria-hidden="true">
      <circle cx="22" cy="25" r="18" fill="#fff"/><path d="M22 14v12h8" stroke="#000" stroke-width="4" fill="none"/>
      <path d="M100 6 L62 24 L80 26 L82 44 Z" fill="#fff"/>
      <circle cx="150" cy="25" r="21" fill="none" stroke="#fff" stroke-width="5"/>
      <rect x="140" y="24" width="20" height="14" fill="#fff"/><path d="M144 24v-6a6 6 0 0 1 12 0v6" stroke="#fff" stroke-width="4" fill="none"/>
      <rect x="205" y="10" width="76" height="32" rx="4" fill="none" stroke="#fff" stroke-width="4"/>
      <rect x="211" y="16" width="64" height="20" fill="#fff"/><rect x="283" y="19" width="6" height="14" fill="#fff"/>
    </svg>
  </div>

  <header class="app-header">
    <svg class="back" width="40" height="76" viewBox="0 0 40 76" aria-label="Back"><path d="M34 4 L6 38 L34 72" stroke="#fff" stroke-width="8" fill="none"/></svg>
    <h1 class="title">Quill Apps</h1>
    <svg class="menu" width="78" height="56" viewBox="0 0 78 56" aria-label="Menu">
      <rect y="0" width="78" height="8" fill="#fff"/><rect y="24" width="78" height="8" fill="#fff"/><rect y="48" width="78" height="8" fill="#fff"/>
    </svg>
  </header>

  <div class="question-bar">
    <div class="counter">QUESTION 7 OF 100</div>
    <svg class="next-arrow" width="30" height="56" viewBox="0 0 30 56" aria-label="Next"><path d="M4 4 L26 28 L4 52" stroke="#1fb53a" stroke-width="5" fill="none"/></svg>
  </div>

  <div class="backdrop" role="img" aria-label="Softly blurred photo of smiling students studying together"></div>

  <div class="question-mark">?</div>
  <p class="question-bubble">A patient presents to the emergency room with the following symptoms: Anxiety, dyspnea, rhonchi, fever, Oxygen saturation of 88%, and a pH of 7.21. The nurse realized that the patient suffering from:</p>

  <div class="option option-a">A. Respiratory alkalosis
    <svg class="mark" width="73" height="73" viewBox="0 0 73 73" aria-hidden="true"><circle cx="36.5" cy="36.5" r="36" fill="#1e7a30"/><path d="M24 24 L49 49 M49 24 L24 49" stroke="#0b0b0b" stroke-width="6"/></svg>
  </div>
  <div class="option option-b">B. Metabolic alkalosis
    <svg class="mark" width="73" height="73" viewBox="0 0 73 73" aria-hidden="true"><circle cx="36.5" cy="36.5" r="36" fill="#1e7a30"/><path d="M24 24 L49 49 M49 24 L24 49" stroke="#0b0b0b" stroke-width="6"/></svg>
  </div>
  <div class="option option-c">C. Respiratory acidosis
    <svg class="mark" width="73" height="73" viewBox="0 0 73 73" aria-hidden="true"><circle cx="36.5" cy="36.5" r="36" fill="#0f3316"/><path d="M22 37 L32 47 L52 26" stroke="#fff" stroke-width="6" fill="none"/></svg>
  </div>
  <div class="option option-d">D. Metabolic acidosis
    <svg class="mark" width="73" height="73" viewBox="0 0 73 73" aria-hidden="true"><circle cx="36.5" cy="36.5" r="36" fill="#0f3316"/><path d="M24 24 L49 49 M49 24 L24 49" stroke="#fff" stroke-width="6"/></svg>
  </div>

  <p class="explanation"><span class="verdict">The correct answer is C.</span> A key symptom of respiratory distress syndrome is the inability of the respiratory system to exchange gases, resulting in respiratory acidosis.</p>

  <div class="action action-save">SAVE &amp; CLOSE</div>
  <div class="action action-next">NEXT QUESTION</div>
</main>
</body>
</html>
```